Open Now Poster for Retail Shop windows.

To design a poster to be printed to put on the windows of our retail stores to tell customers that we are open. Size is to be 590mm W x 840mm H supplied as a pdf. Design should incorporate our logo as well as other elements which indicate the style of our shop which is Womens Beach, Resort & Casual Clothing, Swimwear and Accessories. I would like the design to incorporate the words "Open Now" in some form in large lettering. I would also like the poster to be timeless and able to be used for other wording, so no images would be preferable.

Target Market(s)

Womens Beach, Resort & Casual Clothing, Swimwear and Accessories

Industry/Entity Type

Retail

Colors
e34297

Requirements
Must have
• words "Open Now". as well as our logo.

```html
<!DOCTYPE html>
<html lang="en">
<head>
<meta charset="utf-8">
<title>Open Now – Window Poster</title>
<link rel="stylesheet" href="https://fonts.googleapis.com/css2?family=Russo+One&display=swap">
<style>
  :root {
    --brand-pink: #ec008c;
    --brand-pink-deep: #c21f87;
    --paper: #ffffff;
  }
  html, body {
    margin: 0;
    padding: 0;
    width: 857px;
    height: 1200px;
    overflow: hidden;
    background: var(--paper);
  }
  .poster {
    position: relative;
    width: 857px;
    height: 1200px;
    background: var(--paper);
    font-family: "Russo One", "Arial Black", sans-serif;
  }
  .poster-frame {
    position: absolute;
    left: 47px;
    top: 71px;
    width: 752px;
    height: 884px;
    border: 5px solid var(--brand-pink);
  }
  .poster-art {
    position: absolute;
    inset: 0;
    width: 857px;
    height: 1200px;
  }
  .headline-open {
    fill: var(--paper);
    font-size: 196px;
  }
  .headline-now-box {
    fill: var(--paper);
  }
  .headline-now {
    fill: var(--brand-pink);
    font-size: 196px;
  }
  .brand-name {
    position: absolute;
    left: 0;
    right: 0;
    top: 1008px;
    margin: 0;
    text-align: center;
    color: var(--brand-pink);
    font-size: 86px;
    line-height: 1;
    letter-spacing: 1px;
  }
</style>
</head>
<body>
<main class="poster">
  <div class="poster-frame"></div>

  <svg class="poster-art" viewBox="0 0 857 1200" xmlns="http://www.w3.org/2000/svg">
    <defs>
      <linearGradient id="backdrop-gradient" x1="0" y1="0" x2="0.5" y2="1">
        <stop offset="0" stop-color="#ec008c"/>
        <stop offset="0.65" stop-color="#ec008c"/>
        <stop offset="1" stop-color="#c21f87"/>
      </linearGradient>
    </defs>

    <rect class="headline-backdrop" role="img"
          aria-label="Bold pink paint brush stroke behind the headline"
          x="62" y="125" width="732" height="800" rx="28"
          fill="url(#backdrop-gradient)"/>

    <text class="headline-open" x="149" y="500" textLength="557" lengthAdjust="spacingAndGlyphs">OPEN</text>

    <rect class="headline-now-box" x="149" y="519" width="554" height="184"/>
    <text class="headline-now" x="162" y="685" textLength="528" lengthAdjust="spacingAndGlyphs">NOW</text>
  </svg>

  <p class="brand-name">sunlily</p>
</main>
</body>
</html>
```